Business Card- Can you make it cool vs boring!

Need a refresh on my business card! Want it to be modern but simple, classic and a pop of coolness! we do senior living and it is boring. but that doesn't mean our business card have to look boring! Open to two sided cards. our website is www.Dunmere-PK.com

Target Market(s)

capital market

Industry/Entity Type

senior housing/ real estate

Contact Information for Business Card

logo/ name/ cell/ address/ www.Dunmere-PK.com/ space for a QR code

Requirements
Must have
• maybe a QR code (do not make prominent I may not use the QR so design where it can be taken out) that link to more about us/ landing page. needs to be modern but clean
Should not have
• clip art or script

```html
<!DOCTYPE html>
<html lang="en">
<head>
<meta charset="utf-8">
<title>Dunmere Park – Business Card</title>
<link rel="stylesheet" href="https://fonts.googleapis.com/css2?family=Montserrat:wght@400;500;700&display=swap">
<style>
  :root {
    --stage: #383838;
    --rust: #ae5026;
    --paper: #ffffff;
    --ink: #1e1e1e;
  }
  * { margin: 0; padding: 0; box-sizing: border-box; }
  html, body {
    width: 1200px; height: 1200px; overflow: hidden;
    background: var(--stage);
    font-family: "Montserrat", Arial, sans-serif;
  }
  .canvas { position: relative; width: 1200px; height: 1200px; }

  .card {
    position: absolute; left: 207px; width: 784px; height: 451px;
    border-radius: 26px; overflow: hidden;
  }
  .card--front { top: 129px; background: var(--rust); }
  .card--back  { top: 620px; left: 210px; background: var(--paper); }

  .brand-name {
    position: absolute; font-weight: 500; white-space: nowrap; letter-spacing: 0.01em;
  }
  .card--front .brand-name {
    left: 0; right: 0; top: 170px; text-align: center;
    font-size: 78px; color: var(--paper);
  }
  .card--back .brand-name {
    left: 30px; top: 52px; font-size: 50px; color: var(--rust);
  }

  .person {
    position: absolute; right: 33px; top: 222px; text-align: right;
  }
  .person__name {
    font-weight: 700; font-size: 32px; color: var(--rust); line-height: 1; letter-spacing: 0.005em;
  }
  .person__title {
    margin-top: 10px; font-size: 21px; color: var(--ink); line-height: 1;
  }
  .divider {
    position: absolute; left: 31px; top: 273px; width: 522px; height: 2px; background: var(--rust);
  }
  .accent-bar {
    position: absolute; right: 0; top: 220px; width: 16px; height: 65px; background: var(--rust);
  }

  .contacts { position: absolute; left: 31px; top: 314px; list-style: none; }
  .contacts li {
    display: flex; align-items: center; gap: 8px;
    font-size: 21px; color: var(--ink); height: 32px;
  }
  .contacts svg { width: 18px; height: 18px; fill: var(--rust); flex: none; }

  .address {
    position: absolute; right: 33px; top: 346px; text-align: right;
    font-size: 21px; color: var(--ink); line-height: 32px; font-style: normal;
  }
  .base-band {
    position: absolute; left: 0; right: 0; bottom: 0; height: 21px; background: var(--rust);
  }
</style>
</head>
<body>
<div class="canvas">

  <section class="card card--front">
    <div class="brand-name">Dunmere Park</div>
  </section>

  <section class="card card--back">
    <div class="brand-name">Dunmere Park</div>

    <div class="person">
      <div class="person__name">DOUGLAS HARTWELL</div>
      <div class="person__title">General Manager</div>
    </div>
    <div class="divider"></div>
    <div class="accent-bar"></div>

    <ul class="contacts">
      <li>
        <svg viewBox="0 0 24 24" aria-hidden="true"><path d="M2 9c0-3 4-5 10-5s10 2 10 5v2h-5V8.5c-1.5-.6-3-.8-5-.8s-3.5.2-5 .8V11H2z"/><path d="M5 12l3-3h8l3 3v8H5z"/></svg>
        (555) 214-3087
      </li>
      <li>
        <svg viewBox="0 0 24 24" aria-hidden="true"><path d="M2 5h20v14H2z M3.5 6.5L12 13l8.5-6.5" stroke="#fff" stroke-width="1.5"/></svg>
        info@dunmere-pk.com
      </li>
      <li>
        <svg viewBox="0 0 24 24" aria-hidden="true"><circle cx="12" cy="12" r="10"/><path d="M6 7c2 0 3 1 3 3s-2 2-2 4 1 3 0 5M14 4c0 2 2 2 3 4s-1 3 1 5 2 3 2 3" stroke="#fff" stroke-width="1.4" fill="none"/></svg>
        www.Dunmere-PK.com
      </li>
    </ul>

    <address class="address">
      4810 Cedar Hollow Drive, Suite 1204<br>
      Maple Ridge, TX 77415
    </address>

    <div class="base-band"></div>
  </section>

</div>
</body>
</html>
```